Brochure for a paper wholesaler who wants to educate his print industry clients

We will be making a stapled informative brochure, that contains basic information about our paper products - the types of paper there is, their characteristics and other useful information.
As we are part of a paper wholesaler group in Europe - ORVALT, we received a brochure in German that has this kind of information. The text in it is not as important. What is important is the layout of the document and how the text will appear in it (added in the uploaded files - 210915_Wiessenswertes_TBKU_H73.pdf).
We are allowed to tinker with this file and adjust it to our needs. So there are also .idml and .indd files available (also in the uploaded files).
We would like to keep the custom page size of 210 x290mm (8.3x11.4 in), or you can go up to 210x297mm (8.3x11.7 in).
What we want is a modern looking design that contains our companies red bordo and white/ grey colours to replace the existing green colours in this borchure. The pictures and appearance of the file can be changed according to your views and what you think would look good. We don't necessarily want to keep the same design, we just want the layout of the document be the same, as we will be placing our translated text into it. The ORVALT logo should be replaced with our own logo (KENDRO Logo.png).
As for how it could look, it could go together with our paper presentation, for which the design can be seen in the "KENDRO Base - v2.pptx".
Holiday season, so have a lot of tasks to take care of and not as much time to check MakerHive as often.

```html
<!DOCTYPE html>
<html lang="de">
<head>
<meta charset="utf-8">
<title>Broschüre – Seite 6–7</title>
<link href="https://fonts.googleapis.com/css2?family=Poppins:wght@400;500;600;700;800&display=swap" rel="stylesheet">
<style>
  :root{
    --bg:#111111;
    --paper:#ffffff;
    --bordo:#8a2d33;
    --ink:#1d1d1d;
    --row-dark:#dcdcdc;
    --row-light:#ececec;
  }
  *{box-sizing:border-box;margin:0;padding:0}
  html,body{width:1200px;height:1200px;overflow:hidden;background:var(--bg);font-family:'Poppins',sans-serif;color:var(--ink)}
  .page{position:absolute;top:166px;width:569px;height:786px;background:var(--paper)}
  .page--left{left:29px}
  .page--right{left:605px}
  .abs{position:absolute}
  .rule{height:2px;background:var(--bordo)}
  .page-title{font-weight:800;font-size:18.5px;color:var(--bordo);letter-spacing:-.1px;line-height:1}
  .subhead{font-weight:600;font-size:9.6px;line-height:1}
  .page-no{font-size:7px;font-weight:700;color:var(--bordo)}

  table{border-collapse:collapse;table-layout:fixed}
  .weights th{background:var(--bordo);color:#fff;font-weight:400;font-size:8.6px;line-height:1.2;border-left:1px solid #fff;text-align:center}
  .weights th:first-child{border-left:none}
  .weights td{font-size:8.6px;text-align:center;border-left:1px solid #fff;height:19.8px;padding:0}
  .weights td:first-child{border-left:none;font-weight:700}
  .weights tr:nth-child(odd) td{background:var(--row-dark)}
  .weights tr:nth-child(even) td{background:var(--row-light)}
  .weights--paper th:first-child{text-align:left;padding-left:7px}
  .vertical{writing-mode:vertical-rl;transform:rotate(180deg);display:inline-block;font-size:8.6px}

  .formula{font-size:9.6px;display:flex;align-items:center}
  .fraction{display:inline-flex;flex-direction:column;align-items:center}
  .fraction .num{border-bottom:1px solid var(--ink);padding:0 1px 2px}
  .fraction .den{padding-top:4px}

  .notes td{font-size:9.6px;line-height:13.4px;vertical-align:middle;padding:0 6px}
  .notes td.label{width:94px;border-right:1.5px solid var(--bordo)}
  .notes td.top{vertical-align:top;padding-top:6px}
  .notes tr:nth-child(odd) td{background:var(--row-dark)}
  .notes tr:nth-child(even) td{background:var(--row-light)}

  .brand{display:flex;align-items:center;gap:18px}
  .brand-mark{width:24px;height:30px;border:2px solid var(--bordo)}
  .brand-name{font-size:12px;font-weight:500;color:var(--bordo);letter-spacing:15px}
  .tagline{font-size:7px;font-weight:600;letter-spacing:1.1px}
</style>
</head>
<body>

<section class="page page--left">
  <div class="abs rule" style="left:46px;top:36px;width:482px"></div>
  <h1 class="abs page-title" style="left:46px;top:49px">HILFE BEI GEWICHTSPROBLEMEN</h1>
  <h2 class="abs subhead" style="left:46px;top:76px">Gewichte für Papier-/Kartonformate</h2>

  <table class="abs weights weights--paper" style="left:47px;top:90px;width:482px">
    <colgroup><col style="width:101px"><col><col><col><col><col></colgroup>
    <thead><tr style="height:30px">
      <th>Papiergewicht g/qm</th><th>DIN A6<br>105&nbsp; x 148 mm</th><th>DIN lang<br>100 x 210 mm</th><th>DIN A5<br>148 x 210 mm</th><th>DIN A4<br>210 x 297 mm</th><th>DIN A3<br>297 x 420 mm</th>
    </tr></thead>
    <tbody>
      <tr><td>70</td><td>1,1 g</td><td>1,5 g</td><td>2,2 g</td><td>4,4 g</td><td>8,8 g</td></tr>
      <tr><td>80</td><td>1,3 g</td><td>1,7 g</td><td>2,5 g</td><td>5,0 g</td><td>10,0 g</td></tr>
      <tr><td>90</td><td>1,4 g</td><td>1,9 g</td><td>2,8 g</td><td>5,6 g</td><td>11,2 g</td></tr>
      <tr><td>100</td><td>1,6 g</td><td>2,1 g</td><td>3,2 g</td><td>6,3 g</td><td>12,5 g</td></tr>
      <tr><td>120</td><td>1,9 g</td><td>2,6 g</td><td>3,8 g</td><td>7,5 g</td><td>15,0 g</td></tr>
      <tr><td>150</td><td>2,4 g</td><td>3,2 g</td><td>4,7 g</td><td>9,4 g</td><td>18,7 g</td></tr>
      <tr><td>170</td><td>2,7 g</td><td>3,6 g</td><td>5,3 g</td><td>10,7 g</td><td>21,2 g</td></tr>
      <tr><td>200</td><td>3,1 g</td><td>4,2 g</td><td>6,2 g</td><td>12,5 g</td><td>25,0 g</td></tr>
      <tr><td>250</td><td>3,9 g</td><td>5,2 g</td><td>7,8 g</td><td>15,6 g</td><td>31,2 g</td></tr>
      <tr><td>300</td><td>4,7 g</td><td>6,3 g</td><td>9,3 g</td><td>18,7 g</td><td>37,4 g</td></tr>
    </tbody>
  </table>

  <h2 class="abs subhead" style="left:46px;top:329px">Berechnung des Gewichts eines Bogens (G)</h2>
  <div class="abs formula" style="left:46px;top:348px">
    <span style="margin-top:-2px">(G)g=&nbsp;</span>
    <span class="fraction"><span class="num">Länge (mm) x Breite (mm) x Quadratmetergewicht (g/qm)</span><span class="den">1.000.000</span></span>
  </div>

  <h2 class="abs subhead" style="left:46px;top:388px">Gewichte für Briefumschläge und Versandtaschen</h2>

  <table class="abs weights weights--env" style="left:47px;top:407px;width:482px">
    <colgroup><col style="width:29px"><col><col><col><col><col><col><col></colgroup>
    <thead><tr style="height:104px">
      <th><span class="vertical">Papiergewicht g/qm</span></th>
      <th>DIN C6<br>114&nbsp; x 162<br>mm</th><th>DIN lang<br>110 x 220<br>mm</th><th>DIN C6/5<br>114 x 229<br>mm</th><th>Kompakt-<br>brief<br>125 x 235<br>mm</th><th>DIN C5<br>162&nbsp; x 229<br>mm</th><th>DIN C4<br>229 x 324<br>mm</th><th>Quadra-<br>tisches<br>Format<br>220 x 220<br>mm</th>
    </tr></thead>
    <tbody>
      <tr><td>60</td><td>2,8 g</td><td>3,6 g</td><td>3,9 g</td><td>4,4 g</td><td>5,6 g</td><td>11,1 g</td><td>7,3 g</td></tr>
      <tr><td>70</td><td>3,2 g</td><td>4,2 g</td><td>4,6 g</td><td>5,1 g</td><td>6,5 g</td><td>13,0 g</td><td>8,5 g</td></tr>
      <tr><td>75</td><td>3,5 g</td><td>4,5 g</td><td>4,9 g</td><td>5,5 g</td><td>7,0 g</td><td>13,9 g</td><td>9,1 g</td></tr>
      <tr><td>80</td><td>3,7 g</td><td>4,8 g</td><td>5,2 g</td><td>5,9 g</td><td>7,4 g</td><td>14,8 g</td><td>9,7 g</td></tr>
      <tr><td>90</td><td>4,2 g</td><td>5,5 g</td><td>5,9 g</td><td>6,6 g</td><td>8,4 g</td><td>16,7 g</td><td>10,9 g</td></tr>
      <tr><td>100</td><td>4,6 g</td><td>6,1 g</td><td>6,5 g</td><td>7,3 g</td><td>9,3 g</td><td>18,6 g</td><td>12,1 g</td></tr>
      <tr><td>110</td><td>5,1 g</td><td>6,7 g</td><td>7,2 g</td><td>8,1 g</td><td>10,2 g</td><td>20,4 g</td><td>13,3 g</td></tr>
      <tr><td>120</td><td>5,5 g</td><td>7,3 g</td><td>7,8 g</td><td>8,8 g</td><td>11,1 g</td><td>22,3 g</td><td>14,5 g</td></tr>
    </tbody>
  </table>

  <h2 class="abs subhead" style="left:46px;top:687px">Berechnung des Gewichts einer Hülle (G)</h2>
  <div class="abs formula" style="left:46px;top:704px">
    <span style="margin-top:2px">(G)g=</span>
    <span class="fraction"><span class="num">Länge (mm) x Breite (mm) x Quadratmetergewicht (g/qm) x 2,5</span><span class="den">1.000.000</span></span>
  </div>

  <span class="abs page-no" style="left:28px;top:751px">6</span>
</section>

<section class="page page--right">
  <div class="abs rule" style="left:39px;top:36px;width:530px"></div>
  <h1 class="abs page-title" style="left:39px;top:49px">DIE FEINE ART ZU DRUCKEN</h1>
  <h2 class="abs subhead" style="left:42px;top:76px">Verarbeitungshinweise für Feinstpapiere</h2>
  <h2 class="abs subhead" style="left:42px;top:93px">Druck</h2>

  <table class="abs notes" style="left:42px;top:112px;width:480px">
    <tr style="height:38.5px"><td class="label">Druckfarben:</td><td>Die von den Farbherstellern empfohlenen Farbserien für Naturpapiere sollten angewendet werden.</td></tr>
    <tr style="height:48px"><td class="label">Farbreihenfolge:</td><td>Bei Einfarbmaschinen: Cyan, Magenta, Yellow, Black<br>Bei Zweifarbmaschinen: Cyan – Magenta, Black – Yellow<br>Bei Vierfarbmaschinen: Black – Cyan – Magenta – Yellow</td></tr>
    <tr style="height:63px"><td class="label">Trocknung:</td><td>Durch das Wegschlagen der Farben kann mit einer längeren Trocknungszeit zu rechnen sein. Unternormalen Umständen ist nach 24 Stunden eine Wei­terverarbeitung problemlos möglich. Trockenstoff beschleunigt den Trock­nungsvorgang. Für die Trocknung der Druckfarbe ist der pH-Wert des Wisch-</td></tr>
    <tr style="height:51.5px"><td class="label">Druck-<br>beistellung</td><td>Durch Erhöhen des Anpressdrucks zwischen Gummituch- und Gegendruck­zylinder ist bei strukturierten Papieren auch in den Vertiefungen ein optimaler Ausdruck gewährleistet.</td></tr>
    <tr style="height:71px"><td class="label">Rupfen:</td><td>Bei bestimmten Feinstpapieren ist eine Neigung zum Rupfen festzustellen, deshalb sollten Farben mit einem hohen Tack-Wert nicht eingesetzt werden. Gegen Rupfen hat sich außerdem auch ein&nbsp; Verschneiden der Farbe mit Drucköl oder Druckpaste bewährt.</td></tr>
    <tr style="height:70px"><td class="label">Rasterweiten:</td><td>Die Oberflächenbeschaffenheit des Papiers ist u.a. entscheidend dafür, mit welcher Rasterweite ein gutes Druckergebnis erzielt werden kann. So könnte für ein raues Material ein 60er-Raster optimal und für eine stark geglättete Oberfläche ein feinerer 80er-Raster eine gute Wahl sein.</td></tr>
  </table>

  <h2 class="abs subhead" style="left:42px;top:467px">Verarbeitungshinweise für Feinstpapiere</h2>
  <h2 class="abs subhead" style="left:42px;top:484px">Druck</h2>

  <table class="abs notes" style="left:42px;top:503px;width:480px">
    <tr style="height:74.5px"><td class="label top">Lackieren:</td><td>Lackierungen schützen Drucke gegen mechanische Einflüsse und können zudem Matt- oder Glanz-effekte erzeugen. Verschiedene Techniken führen zu unterschiedlichen Ergebnissen und müssen je nach gewünschtem Effekt auf das jeweilige Material abgestimmt werden. Dabei sind partielle Lackierungen vollflächigen Lackierungen vorz</td></tr>
    <tr style="height:48px"><td class="label top">Farbreihenfolge:</td><td>Bei Einfarbmaschinen: Cyan, Magenta, Yellow, Black<br>Bei Zweifarbmaschinen: Cyan – Magenta, Black – Yellow<br>Bei Vierfarbmaschinen: Black – Cyan – Magenta – Yellow</td></tr>
    <tr style="height:48.5px"><td class="label top">Trocknung:</td><td>Durch das Wegschlagen der Farben kann mit einer längeren Trocknungszeit zu rechnen sein. Unternormalen Umständen ist nach 24 Stunden eine Weiter­verarbeitung problemlos möglich.</td></tr>
    <tr style="height:51.5px"><td class="label top">Druck-<br>beistellung</td><td>Durch Erhöhen des Anpressdrucks zwischen Gummituch- und Gegendruck­zylinder ist bei strukturierten Papieren auch in den Vertiefungen ein optimaler Ausdruck gewährleistet.</td></tr>
  </table>

  <div class="abs brand" style="left:41px;top:740px">
    <span class="brand-mark"></span>
    <span class="brand-name">NARVO</span>
  </div>
  <span class="abs tagline" style="left:363px;top:752px">PAPER BUILT FOR BETTER PRINT!</span>
  <span class="abs page-no" style="left:539px;top:751px">7</span>
</section>

</body>
</html>
```